Business Card Design Project

See brochure project ID# 3917264 Project # 2558848Sadie's Hotels

Industry/Entity Type

Business

Contact Information for Business Card

Information:Marlow's Inns"Ben & Fa'amele Hoskett, Proprietors"PO Box 4817 Pago Pago, American Samoa, 96799Reservations: info@marlowsinns-example.com www.sadieshotels.comPhone 1-684-555-0147

```html
<!DOCTYPE html>
<html lang="en">
<head>
<meta charset="utf-8">
<title>Marlow's Inns – Business Card</title>
<link rel="stylesheet" href="https://fonts.googleapis.com/css2?family=Lato:wght@400;700;900&display=swap">
<style>
  :root {
    --stage: #2b2b2b;
    --card: #f4f4f4;
    --red: #d0102a;
    --ink: #222222;
    --white: #ffffff;
  }
  * { box-sizing: border-box; margin: 0; padding: 0; }
  html, body {
    width: 1200px; height: 997px; overflow: hidden;
    background: var(--stage);
    font-family: "Lato", Arial, sans-serif;
  }
  .card {
    position: absolute; left: 150px; top: 241px;
    width: 900px; height: 515px;
    background: var(--card);
    border-radius: 22px;
    overflow: hidden;
    box-shadow: 0 18px 40px rgba(0,0,0,.55);
  }
  .brand {
    position: absolute; left: 0; right: 0; top: 58px;
    display: flex; justify-content: center; align-items: center; gap: 14px;
  }
  .brand-dot { width: 18px; height: 18px; border-radius: 50%; background: var(--red); }
  .brand-name { font-weight: 900; font-size: 44px; color: var(--red); letter-spacing: .5px; }
  .band-names {
    position: absolute; left: 0; right: 0; top: 138px; height: 40px;
    background: var(--red);
    display: flex; align-items: center; justify-content: center;
  }
  .owners { color: var(--white); font-weight: 700; font-size: 21px; letter-spacing: .4px; text-transform: uppercase; }
  .role {
    position: absolute; left: 0; right: 0; top: 190px; text-align: center;
    font-weight: 900; font-size: 20px; color: var(--ink); letter-spacing: .4px;
  }
  .address {
    position: absolute; right: 60px; top: 232px; text-align: right;
    color: var(--ink); font-size: 19px; line-height: 1.3;
  }
  .address-company { color: var(--red); font-size: 20px; text-transform: uppercase; letter-spacing: .4px; }
  .band-thin {
    position: absolute; left: 0; right: 0; top: 318px; height: 24px;
    background: var(--red);
  }
  .contacts { position: absolute; left: 50px; top: 380px; list-style: none; }
  .contact {
    display: flex; align-items: center; gap: 12px;
    font-size: 20px; color: var(--ink); margin-bottom: 14px;
  }
  .contact-icon {
    width: 28px; height: 28px; border-radius: 5px; background: var(--red);
    display: flex; align-items: center; justify-content: center;
  }
  .web-tab { position: absolute; right: 0; bottom: 0; width: 470px; height: 82px; }
  .web-text {
    position: absolute; right: 40px; bottom: 24px;
    color: var(--white); font-size: 20px; letter-spacing: 2.5px;
  }
</style>
</head>
<body>
  <article class="card">
    <div class="brand">
      <span class="brand-dot"></span>
      <span class="brand-name">Marlow's Inns</span>
    </div>

    <div class="band-names"><span class="owners">Ben &amp; Fa'amele Hoskett</span></div>
    <p class="role">PROPRIETORS</p>

    <address class="address" style="font-style:normal">
      <div class="address-company">Marlow's Inns</div>
      <div>PO Box 4817 Pago Pago, American</div>
      <div>Samoa, 96799</div>
    </address>

    <div class="band-thin"></div>

    <ul class="contacts">
      <li class="contact">
        <span class="contact-icon">
          <svg width="18" height="18" viewBox="0 0 24 24"><path fill="#fff" d="M6.6 10.8a15.1 15.1 0 0 0 6.6 6.6l2.2-2.2a1 1 0 0 1 1-.25 11.4 11.4 0 0 0 3.6.57 1 1 0 0 1 1 1V20a1 1 0 0 1-1 1A17 17 0 0 1 3 4a1 1 0 0 1 1-1h3.5a1 1 0 0 1 1 1c0 1.25.2 2.45.57 3.57a1 1 0 0 1-.25 1z"/></svg>
        </span>
        1-684-555-0147
      </li>
      <li class="contact">
        <span class="contact-icon">
          <svg width="18" height="18" viewBox="0 0 24 24"><rect x="3" y="5" width="18" height="14" rx="2" fill="#fff"/><path d="M3 6l9 7 9-7" stroke="#d0102a" stroke-width="2" fill="none"/></svg>
        </span>
        info@marlowsinns-example.com
      </li>
    </ul>

    <svg class="web-tab" viewBox="0 0 470 82" preserveAspectRatio="none">
      <path d="M0 82 C20 82 30 0 70 0 H470 V82 Z" fill="var(--red)"/>
    </svg>
    <span class="web-text">www.marlowsinns-example.com</span>
  </article>
</body>
</html>
```